Vantro cards

I am in the auto motive, transportation business I would like a business card that is Something cool, modern edgy, having to do with car culture. I offer towing service for high and exotic cars. I also provide towing for collisions and car accidents. I offer open and enclosed transport nationwide.

Target Market(s)

Car culture people high end auto collectors

Industry/Entity Type

Towing car carrier

Contact Information for Business Card

My company colors black yellow and silver

Font styles to use
Serif

```html
<!DOCTYPE html>
<html lang="en">
<head>
<meta charset="utf-8">
<title>Vantro cards</title>
<link rel="stylesheet" href="https://fonts.googleapis.com/css2?family=Poppins:wght@300;400;500;600&display=swap">
<style>
  :root {
    --page: #0c0c0c;
    --card: #242424;
    --card-edge: #f1d749;
    --yellow: #f3d33f;
    --white: #f2f2f2;
    --silver: #b9b9b9;
    --rule: #4a4a4a;
  }
  * { margin: 0; padding: 0; box-sizing: border-box; }
  html, body {
    width: 1200px; height: 820px; overflow: hidden;
    background: var(--page);
    font-family: "Poppins", sans-serif;
  }
  .stage {
    width: 1200px; height: 820px;
    display: flex; align-items: center; justify-content: center; gap: 50px;
  }
  .card {
    position: relative;
    width: 540px; height: 309px;
    background: var(--card);
    border: 2px solid var(--card-edge);
    border-radius: 3px;
    overflow: hidden;
  }
  /* contact side */
  .brand {
    position: absolute; display: flex; align-items: center; gap: 10px;
    color: var(--white); font-weight: 600; line-height: 1;
  }
  .brand-dot { background: var(--yellow); border-radius: 50%; flex: none; }
  .card-back .brand { top: 54px; right: 50px; font-size: 40px; }
  .card-back .brand-dot { width: 22px; height: 22px; }
  .divider-top {
    position: absolute; left: 40px; right: 40px; top: 142px;
    height: 1px; background: var(--rule);
  }
  .person { position: absolute; left: 40px; top: 162px; }
  .person-name {
    color: var(--yellow); font-weight: 600; font-size: 18px;
    letter-spacing: 0.3px; line-height: 1.15; text-transform: uppercase;
  }
  .person-role { color: var(--white); font-weight: 400; font-size: 14px; line-height: 1.3; }
  .divider-person {
    position: absolute; left: 40px; width: 190px; top: 218px;
    height: 1px; background: var(--rule);
  }
  .contact-list {
    position: absolute; left: 40px; top: 228px; list-style: none;
    color: var(--white); font-size: 13px; font-weight: 400; line-height: 20px;
  }
  .contact-list li { display: flex; align-items: center; gap: 8px; }
  .contact-list svg { width: 13px; height: 13px; flex: none; }
  .address {
    position: absolute; right: 40px; top: 162px; text-align: right;
    color: var(--white); font-size: 13px; font-weight: 300; line-height: 1.4;
  }
  /* brand side */
  .card-front { display: flex; align-items: center; justify-content: center; }
  .card-front .brand { position: static; font-size: 64px; gap: 16px; }
  .card-front .brand-dot { width: 34px; height: 34px; }
</style>
</head>
<body>
<main class="stage">
  <section class="card card-back" aria-label="Business card, contact side">
    <div class="brand"><span class="brand-dot"></span>Vantro</div>
    <div class="divider-top"></div>
    <div class="person">
      <p class="person-name">Marcus Delane</p>
      <p class="person-role">Managing Director</p>
    </div>
    <div class="divider-person"></div>
    <ul class="contact-list">
      <li>
        <svg viewBox="0 0 16 16" aria-hidden="true"><path fill="none" stroke="#f3d33f" stroke-width="2" d="M3 2l3 3-2 2c1 2 3 4 5 5l2-2 3 3-2 2C7 15 1 9 1 4z"/></svg>
        044-555 019 274
      </li>
      <li>
        <svg viewBox="0 0 16 16" aria-hidden="true"><rect x="1" y="3" width="14" height="10" fill="#f3d33f"/><path d="M1 3l7 6 7-6" fill="none" stroke="#242424" stroke-width="1.5"/></svg>
        hello@vantrohaul.com
      </li>
      <li>
        <svg viewBox="0 0 16 16" aria-hidden="true"><g fill="none" stroke="#f3d33f" stroke-width="1.4"><circle cx="8" cy="8" r="6.5"/><ellipse cx="8" cy="8" rx="3" ry="6.5"/><path d="M1.5 8h13M3 4.5h10M3 11.5h10"/></g></svg>
        www.vantrohaul.com
      </li>
    </ul>
    <p class="address">87, Kessler Mill Road<br>31870, Westland</p>
  </section>

  <section class="card card-front" aria-label="Business card, brand side">
    <div class="brand"><span class="brand-dot"></span>Vantro</div>
  </section>
</main>
</body>
</html>
```